Website Redesign Brief for Coolvane Climate Services WA

Creating a clear and concise brief for designers to redesign your website, https://breezelineclimatewa.com.au/, is essential to ensure the project aligns with your vision for a more energetic, friendly, optimistic, and user-friendly website. Below is a sample brief tailored to your request, balancing specificity with flexibility to allow designers to bring their creativity to the table.

Website Redesign Brief for Breezeline Climate WA
1. Project Overview

We are seeking a redesign of our website, https://breezelineclimatewa.com.au/, to create a vibrant, engaging, and user-friendly online presence that reflects our brand’s commitment to providing top-notch air conditioning services in Western Australia. The redesigned website should feel energetic, friendly, and optimistic while maintaining professionalism and improving user experience.
2. Goals and Objectives

Enhance Brand Perception: Convey a modern, approachable, and positive brand identity that resonates with both residential and commercial clients.
Improve User Experience: Simplify navigation, improve accessibility, and ensure a seamless experience across devices (desktop, tablet, mobile).
Increase Engagement: Encourage visitors to explore services, request quotes, and contact us through clear calls-to-action (CTAs).
Boost Conversion Rates: Make it easier for users to find information and take action (e.g., booking services or inquiries).
Showcase Expertise: Highlight our professional air conditioning services, experience, and customer satisfaction in an inviting way.

3. Target Audience

Primary Audience: Homeowners and small business owners in Western Australia seeking air conditioning installation, maintenance, or repair services.
Secondary Audience: Property managers, commercial clients, and real estate professionals looking for reliable HVAC solutions.
Demographics: Ages 25–65, mix of tech-savvy and non-tech-savvy users, located primarily in Perth and surrounding areas.
User Needs: Clear information about services, transparent pricing, easy contact options, and reassurance of quality and reliability.

4. Design Preferences

Tone and Style:

Energetic: Use bold, vibrant colors (e.g., blues, whites, and pops of warm tones like orange or yellow) to evoke energy and optimism.
Friendly: Incorporate approachable language, welcoming imagery, and a clean, uncluttered layout.
Optimistic: Highlight positive customer outcomes (e.g., comfort, energy savings) through visuals and messaging.
Professional yet approachable: Maintain credibility as a trusted service provider while avoiding a cold or overly corporate feel.

Visual Elements:

Use high-quality images of happy customers, comfortable homes/offices, and modern air conditioning units.
Incorporate subtle animations or micro-interactions to add energy (e.g., hover effects on buttons or smooth scrolling).
Avoid overly complex graphics that may slow down the site or distract from usability.

Typography: Clean, modern fonts that are easy to read. Use larger, bold headings for hierarchy and warmth.
Inspiration: Websites like https://www.vorlex.com.au/ (clean and professional) or https://www.tandoraclimatech.com.au/ (user-friendly and modern) but with a more vibrant and welcoming vibe.

5. Functional Requirements

User-Friendly Navigation: Simplify the menu structure to make key pages (e.g., Services, About Us, Contact) easily accessible.
Mobile Responsiveness: Ensure the site is fully optimized for mobile devices, with fast load times and intuitive touch interactions.
Key Features:

Prominent CTAs for requesting quotes, booking services, or contacting the team.
A clear service overview with icons or visuals for each service (e.g., installation, repairs, maintenance).
A testimonials section to showcase customer satisfaction.
An easy-to-use contact form with minimal fields.
Integration with Google Maps for location-based services or office directions.

SEO and Performance: Optimize for search engines (e.g., keywords like “air conditioning Perth”) and ensure fast loading speeds.
Accessibility: Follow WCAG guidelines to ensure the site is usable for all visitors, including those with disabilities.

6. Content Guidance

Existing Content: Review and refine current content from https://breezelineclimatewa.com.au/ to make it concise, engaging, and aligned with the friendly tone.
New Content Ideas:

Add a “Why Choose Us” section highlighting expertise, customer service, and eco-friendly solutions.
Include a FAQ page to address common customer questions.
Create a blog section for tips on air conditioning maintenance or energy efficiency (optional).

Tone of Voice: Conversational, reassuring, and positive. Avoid technical jargon unless clearly explained.

7. Technical Considerations

Platform: Open to recommendations (e.g., WordPress, Wix, or custom-built) but prioritize ease of maintenance and scalability.
Integrations: Ensure compatibility with existing tools (e.g., Google Analytics, CRM for quote requests, or booking systems).
Domain and Hosting: Retain current domain (coolvaneclimatewa.com.au); hosting recommendations welcome.
Timeline: Initial design concepts within [insert timeline, e.g., 2–3 weeks], with full redesign completed by [insert deadline, e.g., 6–8 weeks].
Budget: [Insert budget range or state “flexible, please provide a quote”].

8. Deliverables

Wireframes and mockups for homepage, service pages, and contact page.
Fully responsive website design with all necessary pages.
Style guide (colors, fonts, imagery guidelines).
CMS setup (if applicable) with basic training for content updates.
Testing and optimization for performance and SEO.

9. Success Metrics

Increased time on site and reduced bounce rate.
Higher conversion rates for quote requests and contact form submissions.
Positive user feedback on ease of navigation and overall experience.
Improved search engine rankings for key terms within [insert timeframe, e.g., 3 months].

10. Additional Notes

Please provide a portfolio of similar projects or examples of user-friendly, vibrant websites.
We are open to creative suggestions to make the website stand out in the HVAC industry.
Regular progress updates and collaboration during the design process are appreciated.
Updates

designers are asking for more time

few have requested an extension. I Have extended

Target Market(s)

Primary Audience: Homeowners and small business owners in Western Australia seeking air conditioning installation, maintenance, or repair services. Secondary Audience: Property managers, commercial clients, and real estate professionals looking for reliable HVAC solutions. Demographics: Ages 25–65, mix of tech-savvy and non-tech-savvy users, located primarily in Perth and surrounding areas. User Needs: Clear information about services, transparent pricing, easy contact options, and reassurance of quality and reliability.

Industry/Entity Type

Air Conditioning and Refrigeration (HVAC & R)

Coding

Coded - Design and coding required

Colors
0054AA
0677BA
7BADD7
CADEEF
E8F1F8
59FF00
82FF00
B8FF75
E3FFCB
F4FFEA
F0912C
F2A743
F7CA91
FBE8D2
FDF5EE
EE7325
F08F49
F5BC92
FAE3D3
FDF4ED

Requirements
Must have
• Must have all my current information I currently have on my web page.
Nice to have
• A sales page for people to buy products online

```html
<!DOCTYPE html>
<html lang="en">
<head>
<meta charset="utf-8">
<title>Coolvane Climate Services WA</title>
<link href="https://fonts.googleapis.com/css2?family=Open+Sans:ital,wght@0,400;0,600;0,700;1,400&family=Russo+One&display=swap" rel="stylesheet">
<style>
:root{
  --blue:#0677BA;
  --blue-deep:#0054AA;
  --blue-soft:#CADEEF;
  --blue-pale:#E8F1F8;
  --orange:#EE7325;
  --orange-soft:#F08F49;
  --ink:#1d1d1f;
  --text:#444;
  --grey-bg:#f1f1f1;
  --footer:#333333;
  --footer-deep:#2a2a2a;
  --white:#fff;
}
*{box-sizing:border-box;margin:0;padding:0}
html,body{width:1200px;height:4695px;overflow:hidden}
body{font-family:"Open Sans",Arial,sans-serif;color:var(--text);background:var(--white);position:relative}
.abs{position:absolute}
.display{font-family:"Russo One","Arial Black",sans-serif;color:var(--ink);text-transform:uppercase;white-space:nowrap;font-weight:400}
.eyebrow{color:var(--orange);font-size:14px}
.center{left:0;width:1200px;text-align:center}
.btn{position:absolute;display:flex;align-items:center;justify-content:center;font-weight:700;font-size:14px;letter-spacing:.3px;text-transform:uppercase}
.btn-solid{background:var(--blue);color:var(--white)}
.btn-line{border:2px solid var(--blue);color:var(--blue);background:var(--white)}
.photo{position:absolute}

/* header */
.site-header{position:absolute;top:0;left:0;width:1200px;height:88px;background:var(--white);z-index:2}
.brand{position:absolute;left:131px;top:0;width:157px;height:124px;background:var(--white);border-radius:0 0 80px 80px;display:flex;flex-direction:column;align-items:center;justify-content:center;gap:6px;z-index:3;text-align:center}
.brand-dot{width:26px;height:26px;border-radius:50%;background:var(--orange)}
.brand-name{font-size:12px;font-weight:700;color:var(--blue-deep);line-height:1.25}
.topbar{position:absolute;top:14px;font-size:13px;color:var(--ink);display:flex;align-items:center;gap:8px}
.nav{position:absolute;top:54px;font-size:13.5px;color:var(--ink);text-transform:uppercase}
.nav.active{color:var(--orange)}

/* hero */
.hero{position:absolute;top:88px;left:0;width:1200px;height:552px;background:linear-gradient(90deg,#d6e8f4,#c3dcee)}
.hero-photo{left:565px;top:0;width:635px;height:552px;background:linear-gradient(160deg,#e9eef2 0%,#b9cfe0 45%,#3e6fb6 100%)}
.hero h1{position:absolute;left:143px;top:122px;font-size:33px;line-height:56px}
.hero p{position:absolute;left:143px;top:293px;width:480px;font-size:15px;line-height:27px;color:var(--ink)}

/* about */
.about{position:absolute;top:640px;left:0;width:1200px;height:524px;background:var(--white)}
.about-block{left:126px;top:60px;width:250px;height:212px;background:var(--orange)}
.about-photo{left:144px;top:79px;width:434px;height:366px;background:linear-gradient(135deg,#d9d9d9,#6b5a5e 55%,#8a2b36)}
.about p{position:absolute;left:646px;top:214px;width:420px;font-size:13px;line-height:24px}

/* services */
.services{position:absolute;top:1164px;left:0;width:1200px;height:645px;background:var(--grey-bg)}
.services .lead{position:absolute;top:136px;font-size:15px;line-height:30px;color:var(--ink)}
.card{position:absolute;top:215px;width:288px;height:288px;background:var(--white);box-shadow:0 2px 8px rgba(0,0,0,.08)}
.card .pic{position:absolute;left:7px;top:7px;width:274px;height:199px}
.card .label{position:absolute;left:0;top:220px;width:100%;text-align:center;font-size:15.5px;line-height:27px;color:var(--ink)}
.card.current{background:var(--orange)}
.card.current .label{color:var(--white)}
.arrow{position:absolute;top:341px;width:36px;height:36px;border-radius:50%;display:flex;align-items:center;justify-content:center}

/* why */
.why{position:absolute;top:1809px;left:0;width:1200px;height:551px;background:linear-gradient(90deg,#e8701f,#e7782f)}
.feature{position:absolute;width:440px;height:155px;background:var(--white)}
.feature svg{position:absolute;left:20px;top:30px}
.feature h3{position:absolute;left:94px;top:26px;font-size:15.5px;font-weight:600;color:var(--ink)}
.feature p{position:absolute;left:94px;top:56px;width:330px;font-size:13px;line-height:23px}

/* testimonials */
.reviews{position:absolute;top:2360px;left:0;width:1200px;height:473px}
.quote-card{position:absolute;left:345px;top:170px;width:494px;height:217px;border:2px solid var(--blue-soft);background:var(--white);box-shadow:0 2px 10px rgba(6,119,186,.12)}
.quote-card p{position:absolute;left:36px;top:44px;width:422px;text-align:center;font-style:italic;font-size:12.5px;line-height:24px;color:var(--ink)}
.side-quote{position:absolute;top:212px;font-style:italic;font-size:12.5px;line-height:24px;color:#c4c4c4;overflow:hidden;white-space:nowrap}
.qmark{position:absolute;font-family:Georgia,serif;font-size:40px;color:#d8d8d8;line-height:1}
.dots{position:absolute;top:414px;left:574px;display:flex;gap:4px}
.dots span{width:9px;height:9px;border-radius:50%;border:1.5px solid #888}
.dots span.on{background:var(--orange);border-color:var(--orange)}

/* news */
.news{position:absolute;top:2833px;left:0;width:1200px;height:605px}
.post{position:absolute;top:122px;width:289px}
.post .pic{width:289px;height:197px}
.post .meta{margin-top:30px;font-size:11px;color:var(--orange)}
.post h3{margin-top:14px;font-size:16px;line-height:26px;font-weight:400;color:var(--ink)}
.post p{margin-top:8px;font-size:12.5px;line-height:23px}
.post .more{margin-top:12px;font-size:13.5px;font-weight:700;color:var(--blue);display:flex;align-items:center;gap:6px}

/* contact */
.contact{position:absolute;top:3438px;left:0;width:1200px;height:502px;background:var(--blue)}
.contact-photo{left:600px;top:0;width:600px;height:502px;background:linear-gradient(160deg,#c9d1d8,#9aa4ad 50%,#c9343a 85%,#1c2b55)}
.field{position:absolute;left:144px;width:407px;background:var(--white);font-size:11px;color:#888;padding:14px 13px}

/* brands */
.brands{position:absolute;top:3940px;left:0;width:1200px;height:335px}
.brand-tile{position:absolute;top:182px;width:215px;height:80px;background:var(--white);box-shadow:0 2px 10px rgba(0,0,0,.1);display:flex;align-items:center;justify-content:center;gap:8px;font-weight:700;font-size:17px}

/* footer */
.footer{position:absolute;top:4275px;left:0;width:1200px;height:420px;background:var(--footer);color:#e8e8e8}
.footer h4{position:absolute;font-size:15px;font-weight:600;color:var(--white);text-transform:uppercase}
.footer ul{position:absolute;list-style:none;font-size:13px;line-height:23.5px}
.footer li{display:flex;align-items:center;gap:10px}
.footer li::before{content:"»";color:var(--orange);font-size:13px}
.f-label{font-size:10.5px;color:var(--orange);text-transform:uppercase}
.f-item{position:absolute;left:170px;font-size:13px;line-height:23px}
.social{position:absolute;top:312px;width:30px;height:30px;border-radius:50%;border:1.5px solid var(--orange)}
.copyright{position:absolute;left:0;top:392px;width:1200px;height:28px;background:var(--footer-deep);text-align:center;font-size:12.5px;line-height:28px}
</style>
</head>
<body>

<header class="site-header">
  <div class="brand"><span class="brand-dot"></span><span class="brand-name">Coolvane Climate<br>Services WA</span></div>
  <div class="topbar" style="left:682px">
    <svg width="18" height="13" viewBox="0 0 18 13" fill="none" stroke="#0677BA" stroke-width="1.4"><rect x="1" y="1" width="16" height="11" rx="1"/><path d="M1 1l8 6 8-6"/></svg>
    <span>info@coolvaneclimatewa.com.au</span>
  </div>
  <div class="topbar" style="left:948px">
    <svg width="16" height="16" viewBox="0 0 24 24" fill="none" stroke="#0677BA" stroke-width="1.8"><path d="M22 16.9v3a2 2 0 0 1-2.2 2 19.8 19.8 0 0 1-8.6-3.1 19.5 19.5 0 0 1-6-6A19.8 19.8 0 0 1 2.1 4.2 2 2 0 0 1 4.1 2h3a2 2 0 0 1 2 1.7c.1.9.4 1.8.7 2.7a2 2 0 0 1-.5 2.1L8 9.8a16 16 0 0 0 6 6l1.3-1.3a2 2 0 0 1 2.1-.4c.9.3 1.8.6 2.7.7a2 2 0 0 1 1.7 2z"/></svg>
    <span>0412 555 018</span>
  </div>
  <span class="nav active" style="left:329px">Home</span>
  <span class="nav" style="left:402px">About Us</span>
  <span class="nav" style="left:503px">Services</span>
  <span class="nav" style="left:596px">Cleaning</span>
  <span class="nav" style="left:697px">Regasing</span>
  <span class="nav" style="left:797px">Commissioning</span>
  <span class="nav" style="left:946px">Air Balancing</span>
</header>

<section class="hero">
  <div class="photo hero-photo" role="img" aria-label="Smiling technician in blue overalls giving a thumbs up beneath a wall-mounted air conditioner"></div>
  <span class="abs eyebrow" style="left:143px;top:93px">Welcome To Coolvane Climate Services WA</span>
  <h1 class="display">Quality Air Conditioning<br>Repairs, Service And<br>Installations</h1>
  <p>Our Service Is Second To None; We Have A Team of Experienced Technicians That Consistently Deliver The Best Quality Air Conditioner Repairs Perth Has To Offer.</p>
  <a class="btn btn-solid" style="left:143px;top:406px;width:200px;height:48px">Book A Service</a>
  <a class="btn btn-line" style="left:353px;top:406px;width:215px;height:48px;background:transparent">Quality Services</a>
</section>

<section class="about">
  <div class="abs about-block"></div>
  <div class="photo about-photo" role="img" aria-label="Technician in an orange hard hat servicing a split system unit beside curtains"></div>
  <span class="abs eyebrow" style="left:646px;top:130px">About Us</span>
  <h2 class="display abs" style="left:645px;top:160px;font-size:33px">Need A Technician?</h2>
  <p>Our call out fee includes the first half hour on site. In most cases will be able to diagnose the problem with in that time, and repair it if no parts are required. If any parts, gas or additional labour is required, we will let you know before we proceed.</p>
  <a class="btn btn-solid" style="left:647px;top:347px;width:166px;height:45px;font-size:13px">More About Us</a>
  <a class="btn btn-line" style="left:826px;top:347px;width:151px;height:45px;font-size:13px">Get In Touch</a>
</section>

<section class="services">
  <span class="abs eyebrow center" style="top:51px">What We Offer</span>
  <h2 class="display abs center" style="top:82px;font-size:33px">Our Services</h2>
  <p class="lead center">Please Be Aware That Paying For Your Service Upfront Does Not Mean Next Day Service. Your Service Will However<br>Be Prioritised And Scheduled Into The Next Available Slot.</p>
  <div class="arrow" style="left:88px;background:#777"><svg width="12" height="12" viewBox="0 0 12 12" fill="none" stroke="#fff" stroke-width="1.8"><path d="M8 1L3 6l5 5"/></svg></div>
  <div class="arrow" style="left:1075px;background:var(--blue)"><svg width="12" height="12" viewBox="0 0 12 12" fill="none" stroke="#fff" stroke-width="1.8"><path d="M4 1l5 5-5 5"/></svg></div>
  <div class="card" style="left:144px">
    <div class="pic" role="img" aria-label="Rooftop commercial air conditioning plant" style="background:linear-gradient(180deg,#dfe4e8,#8c959c 60%,#5d6a5d)"></div>
    <div class="label">Commercial Air Conditioning<br>Installation &amp; Repairs</div>
  </div>
  <div class="card current" style="left:456px">
    <div class="pic" role="img" aria-label="Technician installing a domestic split system" style="background:linear-gradient(180deg,#f2f2f2,#c8ccd0 50%,#2b3f66)"></div>
    <div class="label">Domestic Aircon Installation<br>and Repairs</div>
  </div>
  <div class="card" style="left:768px">
    <div class="pic" role="img" aria-label="Coolroom with stainless steel shelving" style="background:linear-gradient(180deg,#d8dcdf,#a9b0b5 60%,#6f7478)"></div>
    <div class="label">Coolroom Installation<br>and Repairs</div>
  </div>
  <a class="btn btn-solid" style="left:507px;top:538px;width:184px;height:42px;font-size:13px">View All Services</a>
</section>

<section class="why">
  <span class="abs center" style="top:55px;color:var(--white);font-size:14px">Coolvane Climate Services WA</span>
  <h2 class="display abs center" style="top:86px;font-size:33px;color:var(--white)">Why Choose Us?</h2>

  <div class="feature" style="left:144px;top:154px">
    <svg width="56" height="62" viewBox="0 0 56 62" fill="none" stroke="#0677BA" stroke-width="2"><circle cx="28" cy="24" r="18" stroke="#EE7325"/><circle cx="28" cy="24" r="11"/><path d="M28 17l2 4.5 5 .5-3.7 3.3 1 4.9-4.3-2.5-4.3 2.5 1-4.9L21 22l5-.5z" stroke="#EE7325"/><path d="M17 38l-6 18 8-4 4 7 5-15M39 38l6 18-8-4-4 7-5-15"/></svg>
    <h3>Experts in Air Conditioning</h3>
    <p>Lorem ipsum dolor sit amet, consectetur adipiscing elit, sed do eiusmod tempor incididunt ut labore et dolore magna aliqua ut enim ad minim</p>
  </div>
  <div class="feature" style="left:615px;top:154px">
    <svg width="64" height="56" viewBox="0 0 64 56" fill="none" stroke="#EE7325" stroke-width="2"><circle cx="34" cy="12" r="9" stroke="#0677BA"/><path d="M30 12l3 3 5-6" stroke="#0677BA"/><path d="M2 28l10-6 10 4 8-3 12 3 10-4 10 6M12 22l-6 16 16 12 6-4M52 22l6 16-14 12-10-6-8-8"/><path d="M26 34l8 8M30 30l8 8"/></svg>
    <h3>Specialist Dealer Network</h3>
    <p>Lorem ipsum dolor sit amet, consectetur adipiscing elit, sed do eiusmod tempor incididunt ut labore et dolore magna aliqua ut enim ad minim</p>
  </div>
  <div class="feature" style="left:144px;top:332px">
    <svg width="60" height="58" viewBox="0 0 60 58" fill="none" stroke="#0677BA" stroke-width="2"><circle cx="30" cy="20" r="8" stroke="#EE7325"/><path d="M30 4v5M30 31v5M14 20h5M41 20h5M19 9l3.5 3.5M37.5 27.5L41 31M41 9l-3.5 3.5M22.5 27.5L19 31" stroke="#EE7325"/><path d="M4 44h10l8 4h14l14-8c3-2 6 1 4 3L40 54H20l-6-3H4z"/></svg>
    <h3>Quality After Support</h3>
    <p>Lorem ipsum dolor sit amet, consectetur adipiscing elit, sed do eiusmod tempor incididunt ut labore et dolore magna aliqua ut enim ad minim</p>
  </div>
  <div class="feature" style="left:615px;top:332px">
    <svg width="56" height="60" viewBox="0 0 56 60" fill="none" stroke="#EE7325" stroke-width="2"><rect x="6" y="4" width="32" height="44" rx="2"/><path d="M13 14h18M13 22h18M13 30h10" stroke="#0677BA"/><circle cx="40" cy="42" r="8" stroke="#0677BA"/><path d="M36 42l3 3 5-6" stroke="#0677BA"/><path d="M34 50l-4 8M46 50l4 8"/></svg>
    <h3>Allergy-Friendly Approved</h3>
    <p>Lorem ipsum dolor sit amet, consectetur adipiscing elit, sed do eiusmod tempor incididunt ut labore et dolore magna aliqua ut enim ad minim</p>
  </div>
</section>

<section class="reviews">
  <span class="abs eyebrow center" style="top:80px">Reviews</span>
  <h2 class="display abs center" style="top:112px;font-size:33px">Customers Testimonials</h2>
  <div class="side-quote" style="left:176px;width:166px;text-align:right">Fantastic job! Liam and Rory<br>kept me informed and provided<br>the costs to</div>
  <div class="side-quote" style="left:843px;width:200px">professionalism and honesty. He<br>was not required after checking<br>and fixed other items.</div>
  <div class="quote-card">
    <span class="qmark" style="left:16px;top:14px">&ldquo;</span>
    <span class="qmark" style="left:298px;top:96px">&rdquo;</span>
    <p>Thank you Liam and Marco for installing our 18kW Vorlex. My brother is a fridgy tech and looked over the install for me. I said its near perfect. Thank you.</p>
    <div class="abs" role="img" aria-label="Customer photo" style="left:118px;top:134px;width:54px;height:54px;border-radius:50%;background:linear-gradient(135deg,#c9a27a,#6d5440)"></div>
    <span class="abs" style="left:188px;top:140px;font-size:13px;color:var(--ink)">Daniel Reyes</span>
    <svg class="abs" style="left:188px;top:164px" width="84" height="14" viewBox="0 0 84 14" fill="#F2A743">
      <path id="star" d="M7 0l2 4.5 5 .5-3.7 3.3 1 4.9L7 10.7 2.7 13.2l1-4.9L0 5l5-.5z"/>
      <use href="#star" x="17"/><use href="#star" x="34"/><use href="#star" x="51"/><use href="#star" x="68"/>
    </svg>
    <span class="abs" style="right:14px;top:190px;font-size:10.5px;color:#999">5 days ago</span>
  </div>
  <div class="dots"><span></span><span class="on"></span><span></span><span></span></div>
</section>

<section class="news">
  <span class="abs eyebrow center" style="top:26px">Blogs</span>
  <h2 class="display abs center" style="top:57px;font-size:33px">Our Latest News</h2>
  <article class="post" style="left:144px">
    <div class="pic" role="img" aria-label="Technician servicing a ceiling cassette unit" style="background:linear-gradient(180deg,#cfd3d6,#8e9296 55%,#2f3e5e)"></div>
    <div class="meta">&#9638; Feb 29, 2024 &nbsp;/&nbsp; &#9679; By Admin</div>
    <h3>Sed ut perspiciatis unde omnis iste natus error sit voluptatem</h3>
    <p>Lorem ipsum dolor sit amet, consectetur adipiscing elit, sed do eiusmod tempor incididunt ut labore et dolore magna</p>
    <div class="more">LEARN MORE <svg width="12" height="12" viewBox="0 0 12 12"><circle cx="6" cy="6" r="6" fill="#0677BA"/><path d="M5 3.5L7.5 6 5 8.5" stroke="#fff" stroke-width="1.5" fill="none"/></svg></div>
  </article>
  <article class="post" style="left:455px">
    <div class="pic" role="img" aria-label="Aerial view of rooftop condenser units" style="background:linear-gradient(180deg,#e3e0da,#bdb6aa 60%,#8f8a80)"></div>
    <div class="meta">&#9638; Feb 29, 2024 &nbsp;/&nbsp; &#9679; By Admin</div>
    <h3>Sed ut perspiciatis unde omnis iste natus error sit voluptatem</h3>
    <p>Lorem ipsum dolor sit amet, consectetur adipiscing elit, sed do eiusmod tempor incididunt ut labore et dolore magna</p>
    <div class="more">LEARN MORE <svg width="12" height="12" viewBox="0 0 12 12"><circle cx="6" cy="6" r="6" fill="#0677BA"/><path d="M5 3.5L7.5 6 5 8.5" stroke="#fff" stroke-width="1.5" fill="none"/></svg></div>
  </article>
  <article class="post" style="left:766px">
    <div class="pic" role="img" aria-label="Technician checking a rooftop condenser in the city" style="background:linear-gradient(180deg,#b7c7d3,#7b8591 55%,#4a4f55)"></div>
    <div class="meta">&#9638; Feb 29, 2024 &nbsp;/&nbsp; &#9679; By Admin</div>
    <h3>Sed ut perspiciatis unde omnis iste natus error sit voluptatem</h3>
    <p>Lorem ipsum dolor sit amet, consectetur adipiscing elit, sed do eiusmod tempor incididunt ut labore et dolore magna</p>
    <div class="more">LEARN MORE <svg width="12" height="12" viewBox="0 0 12 12"><circle cx="6" cy="6" r="6" fill="#0677BA"/><path d="M5 3.5L7.5 6 5 8.5" stroke="#fff" stroke-width="1.5" fill="none"/></svg></div>
  </article>
</section>

<section class="contact">
  <div class="photo contact-photo" role="img" aria-label="Two technicians with a clipboard and toolbox beside an outdoor condenser unit"></div>
  <span class="abs" style="left:144px;top:50px;color:var(--white);font-size:15px">Get in Touch</span>
  <h2 class="display abs" style="left:143px;top:84px;font-size:33px;color:var(--white)">Contact Us</h2>
  <div class="field" style="top:146px;height:44px">Full Name*</div>
  <div class="field" style="top:204px;height:44px">Email*</div>
  <div class="field" style="top:261px;height:113px">Message*</div>
  <a class="btn" style="left:144px;top:400px;width:166px;height:42px;border:2px solid #fff;color:#fff;font-size:13px">Send Message</a>
</section>

<section class="brands">
  <span class="abs eyebrow center" style="top:77px">Brands</span>
  <h2 class="display abs center" style="top:118px;font-size:33px">Our Recommended Brands</h2>
  <div class="brand-tile" style="left:144px;color:#1f3f73"><span style="width:18px;height:18px;border-radius:50%;background:#0677BA"></span>Ventaro</div>
  <div class="brand-tile" style="left:376px;color:#c62828"><span style="width:16px;height:16px;background:#c62828"></span>Tandora Climatech</div>
  <div class="brand-tile" style="left:607px;color:var(--blue-deep)"><span style="width:16px;height:16px;background:#0677BA"></span>Vorlex</div>
  <div class="brand-tile" style="left:839px;color:#2a6fb5;font-size:15px"><span style="width:18px;height:18px;border-radius:50%;background:#7BADD7"></span>Coolmara International</div>
</section>

<footer class="footer">
  <h4 style="left:144px;top:62px">Contact Us</h4>
  <svg class="abs" style="left:144px;top:96px" width="12" height="12" viewBox="0 0 24 24" fill="#EE7325"><path d="M22 16.9v3a2 2 0 0 1-2.2 2 19.8 19.8 0 0 1-8.6-3.1 19.5 19.5 0 0 1-6-6A19.8 19.8 0 0 1 2.1 4.2 2 2 0 0 1 4.1 2h3a2 2 0 0 1 2 1.7c.1.9.4 1.8.7 2.7a2 2 0 0 1-.5 2.1L8 9.8a16 16 0 0 0 6 6l1.3-1.3a2 2 0 0 1 2.1-.4c.9.3 1.8.6 2.7.7a2 2 0 0 1 1.7 2z"/></svg>
  <span class="f-item f-label" style="top:94px">Phone</span>
  <span class="f-item" style="top:114px">0412 555 018</span>
  <svg class="abs" style="left:144px;top:148px" width="12" height="10" viewBox="0 0 18 13" fill="#EE7325"><rect width="18" height="13" rx="1"/></svg>
  <span class="f-item f-label" style="top:145px">Email</span>
  <span class="f-item" style="top:165px">info@coolvaneclimatewa.com.au</span>
  <svg class="abs" style="left:144px;top:200px" width="12" height="14" viewBox="0 0 12 14" fill="#EE7325"><path d="M6 0a5 5 0 0 1 5 5c0 4-5 9-5 9S1 9 1 5a5 5 0 0 1 5-5z"/><circle cx="6" cy="5" r="2" fill="#333"/></svg>
  <span class="f-item f-label" style="top:199px">Location</span>
  <span class="f-item" style="top:219px">48 Harbourview Lane, Kelso WA 6170</span>
  <svg class="abs" style="left:144px;top:256px" width="13" height="13" viewBox="0 0 14 14" fill="none" stroke="#EE7325" stroke-width="2"><circle cx="7" cy="7" r="6"/><path d="M7 3.5V7l2.5 1.5"/></svg>
  <span class="f-item f-label" style="top:253px">Working Hours</span>
  <span class="f-item" style="top:273px">Mon-Fri: 8.00am to 5.00pm<br>Weekends and Public Holidays:<br>Additional Callout Fee.</span>

  <h4 style="left:476px;top:62px">Quick Links</h4>
  <ul style="left:476px;top:88px"><li>Home</li><li>About</li><li>Service</li><li>Project Works</li><li>Residential Services</li><li>Careers</li><li>Contact</li></ul>
  <h4 style="left:476px;top:276px">Follow Us</h4>
  <span class="social" style="left:480px" aria-label="Social profile"></span>
  <span class="social" style="left:518px;background:var(--orange)" aria-label="Social profile"></span>
  <span class="social" style="left:558px;border-color:#ccc" aria-label="Social profile"></span>

  <h4 style="left:713px;top:62px">Services</h4>
  <ul style="left:713px;top:88px"><li>Commercial Air Conditioning Installation &amp; Repairs</li><li>Domestic Aircon Installation &amp; Repairs</li><li>Coolroom Installation &amp; Repairs</li><li>Chiller Service &amp; Repairs</li><li>Air Quality Control</li><li>BMS Upgrades &amp; Installation</li></ul>
  <h4 style="left:713px;top:252px">Other Links</h4>
  <ul style="left:713px;top:278px"><li>Terms &amp; Conditions</li><li>Privacy Policy</li><li>FAQS</li><li>Contact Us</li></ul>

  <div class="copyright">&copy; 2025 Copyright - Coolvane Climate Services WA. All Rights Reserved</div>
</footer>

</body>
</html>
```